Letterhead for Conveyancing Company

Use existing logo to create a letterhead for a conveyancing company. Must be able to be used in Microsoft Word. Easy to read and professional.
Contact information to be at the bottom.
Bright Oak Conveyancing Pty Ltd
ACN 621 984 736PO Box 535 Campbelltown SA 5074
Mobile - 0461739286
Web address - www.brightoakconveyancing.com.au

Requirements
Must have
• Logo and contact details.
• Simple and professional.

```html
<!DOCTYPE html>
<html lang="en">
<head>
<meta charset="utf-8">
<title>Bright Oak Conveyancing Letterhead</title>
<link href="https://fonts.googleapis.com/css2?family=Open+Sans:wght@400;700;800&display=swap" rel="stylesheet">
<style>
  :root {
    --backdrop: #d5d9da;
    --paper: #ffffff;
    --brand-pink: #e0318e;
    --brand-pink-light: #f7a3cf;
    --ink-grey: #7a7a7a;
    --ink-soft: #555555;
    --watermark: #eeeeee;
    --rule: #cfcfcf;
  }
  * { margin: 0; padding: 0; box-sizing: border-box; }
  html, body {
    width: 1200px; height: 784px; overflow: hidden;
    background: var(--backdrop);
    font-family: "Open Sans", Arial, sans-serif;
  }
  .letterhead {
    position: absolute;
    left: 338px; top: 22px;
    width: 524px; height: 740px;
    background: var(--paper);
    box-shadow: 0 4px 18px rgba(0,0,0,0.12);
    overflow: hidden;
  }
  .corner-swoosh {
    position: absolute; top: 0; right: 0;
    width: 200px; height: 170px;
  }
  .brand-header {
    position: absolute;
    top: 88px; right: 22px;
    display: flex; align-items: center; gap: 12px;
  }
  .brand-name {
    font-weight: 800;
    color: var(--ink-grey);
    font-size: 17px;
    line-height: 1.05;
    text-align: right;
    letter-spacing: -0.2px;
  }
  .brand-name span { display: block; }
  .brand-name .brand-sub { font-size: 9.5px; letter-spacing: 2.2px; }
  .contact-list {
    list-style: none;
    border-left: 1px solid var(--rule);
    padding-left: 9px;
    font-size: 6.4px;
    line-height: 1.9;
    color: var(--ink-soft);
  }
  .contact-list li { display: flex; align-items: center; gap: 4px; white-space: nowrap; }
  .contact-list .contact-address { color: var(--brand-pink); font-weight: 700; }
  .contact-dot {
    width: 5px; height: 5px; border-radius: 50%;
    background: var(--brand-pink-light); flex: none;
  }
  .watermark-name {
    position: absolute;
    left: 28px; bottom: 150px;
    font-weight: 800;
    font-size: 40px;
    line-height: 0.95;
    color: var(--watermark);
  }
</style>
</head>
<body>
  <main class="letterhead">
    <svg class="corner-swoosh" viewBox="0 0 200 170" aria-hidden="true">
      <defs>
        <linearGradient id="swooshFill" x1="0" y1="0" x2="1" y2="1">
          <stop offset="0" stop-color="#e0318e"/>
          <stop offset="1" stop-color="#f7a3cf"/>
        </linearGradient>
      </defs>
      <path d="M0 0 H200 V170 C190 95 130 20 0 0 Z" fill="url(#swooshFill)"/>
      <path d="M20 0 C135 18 185 80 200 150 V170 C188 92 128 22 0 0 Z" fill="#ffffff" opacity="0"/>
    </svg>

    <header class="brand-header">
      <div class="brand-name">
        <span>Bright Oak</span>
        <span class="brand-sub">CONVEYANCING</span>
      </div>
      <ul class="contact-list">
        <li class="contact-address"><i class="contact-dot"></i>PO Box 871 Marlowdale SA 5096</li>
        <li><i class="contact-dot"></i>ACN 583 217 469 &nbsp;<i class="contact-dot"></i>0461739286</li>
        <li><i class="contact-dot"></i>contact@brightoakconveyancing.com.au</li>
        <li><i class="contact-dot"></i>www.brightoakconveyancing.com.au</li>
      </ul>
    </header>

    <div class="watermark-name" aria-hidden="true">Bright<br>Oak</div>
  </main>
</body>
</html>
```